Granite Bureau of Analysis Card Design

I need a business card for the agency I currently am tasked with, which is based in Hartford, CT. GBAN provides, disseminates and obtains intelligence in regards to ongoing criminal investigations throughout the State of CT. The information we obtain and provide, comes to us and is sent out by various Law Enforcement agencies throughout CT.

Industry/Entity Type

Business

Contact Information for Business Card

Officer Lyle P. Harrowby
Bramford Police Department - Eastern Region Intelligence Officer
Granite Bureau of Analysis
4827 Willowmere Ave., Middletown, CT 06457
Work Cell: (555) 318-2694
E-Mail: gban.wd@gbanmail.example

```html
<!DOCTYPE html>
<html lang="en">
<head>
<meta charset="utf-8">
<title>Granite Bureau of Analysis – Business Card</title>
<link rel="stylesheet" href="https://fonts.googleapis.com/css2?family=PT+Sans:wght@400;700&display=swap">
<style>
  :root {
    --backdrop: #e4e2df;
    --card: #ffffff;
    --card-shade: #ececec;
    --brand-red: #bf2a26;
    --brand-yellow: #e8cf3a;
    --ink: #3a3a3a;
    --ink-soft: #555555;
    --on-red: #ffffff;
    --badge-ink: #1c1c1c;
  }
  * { margin: 0; padding: 0; box-sizing: border-box; }
  html, body {
    width: 1200px; height: 899px; overflow: hidden;
    background: var(--backdrop);
    font-family: "PT Sans", Arial, sans-serif;
  }
  .business-card {
    position: absolute; left: 150px; top: 180px;
    width: 900px; height: 540px;
    border-radius: 48px; overflow: hidden;
    background: linear-gradient(180deg, var(--card) 55%, var(--card-shade));
    box-shadow: 0 18px 40px rgba(0,0,0,.18);
  }
  .card-bands { position: absolute; inset: 0; }
  .holder {
    position: absolute; right: 44px; top: 50px; text-align: right;
    color: var(--on-red);
  }
  .holder-name { font-size: 29px; font-weight: 400; letter-spacing: 1.5px; }
  .holder-title { font-size: 18px; margin-top: 6px; line-height: 1.3; }
  .contact-list {
    position: absolute; left: 38px; top: 318px; list-style: none;
    font-size: 15px; color: var(--ink-soft);
  }
  .contact-list li { display: flex; align-items: center; gap: 12px; height: 32px; }
  .contact-list svg { width: 16px; height: 16px; fill: var(--ink); flex: none; }
  .agency-mark {
    position: absolute; left: 330px; top: 290px;
    display: flex; align-items: center; gap: 12px;
    color: var(--badge-ink); font-size: 20px; font-weight: 700; line-height: 1.2;
  }
  .agency-mark .mark-square { width: 26px; height: 26px; background: var(--badge-ink); flex: none; }
  .office-address {
    position: absolute; right: 60px; bottom: 52px; text-align: right;
    font-size: 17px; color: var(--ink); line-height: 1.45;
  }
</style>
</head>
<body>
  <div class="business-card">
    <svg class="card-bands" viewBox="0 0 900 540" preserveAspectRatio="none" aria-hidden="true">
      <path d="M0,0 H900 V255 C720,120 330,70 0,175 Z" fill="var(--brand-red)"/>
      <path d="M0,175 C330,70 720,120 900,255 V285 C720,150 330,95 0,200 Z" fill="var(--brand-yellow)"/>
    </svg>

    <div class="holder">
      <div class="holder-name">OFFICER LYLE P. HARROWBY</div>
      <div class="holder-title">Eastern Region Intelligence Officer<br>Granite Bureau of Analysis</div>
    </div>

    <ul class="contact-list">
      <li><svg viewBox="0 0 16 16"><path d="M4 0h8a1 1 0 0 1 1 1v14a1 1 0 0 1-1 1H4a1 1 0 0 1-1-1V1a1 1 0 0 1 1-1zm1 2v10h6V2z"/></svg>Work Cell: (555) 318-2694</li>
      <li><svg viewBox="0 0 16 16"><path d="M1 3h14v10H1zm1 1v1l6 4 6-4V4z"/></svg>gban.wd@gbanmail.example</li>
      <li><svg viewBox="0 0 16 16"><path d="M8 0a5 5 0 0 1 5 5c0 4-5 11-5 11S3 9 3 5a5 5 0 0 1 5-5zm0 3a2 2 0 1 0 0 4 2 2 0 0 0 0-4z"/></svg>Middletown, CT</li>
    </ul>

    <div class="agency-mark">
      <span class="mark-square"></span>
      <span>Bramford Police<br>Department</span>
    </div>

    <div class="office-address">4827 Willowmere Ave.<br>Middletown, CT 06457</div>
  </div>
</body>
</html>
```